Harbourline Electrical Solutions

On one side. LOGO (underneath:) Commercial Industrial Residential

- NAME & CONTACT DETAILS

Marcus T. Hollings
Project Manager

(Cell icon) (441) 555-0187
(Email icon) hlelectricalsolutions@mailvento.com
(Facebook & Instagram icons )@hlelectricalsolutions

Other side: LOGO - underneath ELECTRICAL CONSTRUCTION & MAINTENANCE . LED LIGHTING & AUTOMATION . LIFE SAFETY SYSTEMS (FIRE ALARM / SECURITY) . DATA & COMMUNICATION

```html
<!DOCTYPE html>
<html lang="en">
<head>
<meta charset="utf-8">
<title>Harbourline Electrical Solutions – Business Card</title>
<link href="https://fonts.googleapis.com/css2?family=Montserrat:wght@400;500;600&display=swap" rel="stylesheet">
<style>
  :root {
    --teal: #13546b;
    --teal-dark: #0f4658;
    --white: #ffffff;
    --ink-gray: #5a5f63;
    --stripe-gray: #4f5254;
    --backdrop: #e4e4e4;
  }
  * { box-sizing: border-box; margin: 0; padding: 0; }
  html, body {
    width: 1200px; height: 930px; overflow: hidden;
    background: var(--backdrop);
    font-family: "Montserrat", sans-serif;
  }
  .sheet {
    position: relative; width: 1200px; height: 930px;
  }
  .card {
    position: absolute; left: 240px;
    width: 720px; height: 411px;
    border-radius: 26px; overflow: hidden;
  }
  /* Front side */
  .card--front { top: 40px; background: var(--teal); color: var(--white); }
  .front-brand {
    position: absolute; left: 150px; top: 78px;
    display: flex; align-items: center; gap: 22px;
  }
  .brand-square {
    width: 58px; height: 58px; background: var(--white);
  }
  .brand-name {
    font-weight: 500; font-size: 30px; line-height: 1.08;
    letter-spacing: 3px; text-transform: uppercase;
  }
  .services {
    position: absolute; left: 150px; top: 250px;
    list-style: none; font-weight: 500; font-size: 17px;
    letter-spacing: 1.4px; line-height: 1.5; text-transform: uppercase;
  }
  .services li::before { content: "•"; margin-right: 12px; }

  /* Back side */
  .card--back { top: 480px; background: var(--white); }
  .social {
    position: absolute; left: 40px; top: 56px;
    display: flex; align-items: center; gap: 10px;
    color: var(--ink-gray); font-size: 17px; letter-spacing: 0.5px;
  }
  .social-square { width: 18px; height: 18px; background: var(--teal); border-radius: 3px; }
  .back-brand {
    position: absolute; right: 40px; top: 40px; text-align: right; color: var(--teal);
  }
  .back-brand .brand-line { display: flex; align-items: center; justify-content: flex-end; gap: 12px; }
  .back-brand .brand-square { width: 34px; height: 34px; background: var(--teal); }
  .back-brand .brand-name { font-size: 17px; letter-spacing: 2px; }
  .sectors {
    margin-top: 10px; font-weight: 600; font-size: 14px; letter-spacing: 0.8px;
  }
  .person {
    position: absolute; right: 40px; top: 178px; text-align: right;
  }
  .person-name {
    color: var(--teal); font-weight: 600; font-size: 22px; letter-spacing: 1.5px; text-transform: uppercase;
  }
  .person-title { color: var(--ink-gray); font-size: 16px; margin-top: 4px; }
  .rule {
    position: absolute; left: 180px; right: 40px; top: 250px;
    height: 1.5px; background: var(--teal);
  }
  .contacts {
    position: absolute; right: 40px; top: 266px; list-style: none;
    color: var(--ink-gray); font-size: 16px; text-align: right; line-height: 1.75;
  }
  .contacts li { display: flex; align-items: center; justify-content: flex-end; gap: 10px; }
  .contacts svg { width: 16px; height: 16px; }
  .footer-band { position: absolute; left: 0; bottom: 0; width: 720px; height: 70px; }
</style>
</head>
<body>
<main class="sheet">
  <section class="card card--front" aria-label="Card front">
    <div class="front-brand">
      <span class="brand-square" aria-hidden="true"></span>
      <p class="brand-name">Harbourline<br>Electrical<br>Solutions</p>
    </div>
    <ul class="services">
      <li>Data &amp; Communication</li>
      <li>LED Lighting &amp; Automation</li>
      <li>Electrical Construction &amp; Maintenance</li>
      <li>Life Safety Systems (Fire Alarm / Security)</li>
    </ul>
  </section>

  <section class="card card--back" aria-label="Card back">
    <div class="social">
      <span class="social-square" aria-hidden="true"></span>
      <span>@hlelectricalsolutions</span>
    </div>
    <div class="back-brand">
      <div class="brand-line">
        <span class="brand-square" aria-hidden="true"></span>
        <p class="brand-name">Harbourline<br>Electrical<br>Solutions</p>
      </div>
      <p class="sectors">Commercial Industrial Residential</p>
    </div>
    <div class="person">
      <p class="person-name">Marcus T. Hollings</p>
      <p class="person-title">Project Manager</p>
    </div>
    <div class="rule"></div>
    <ul class="contacts">
      <li>(441) 555-0187
        <svg viewBox="0 0 24 24" aria-hidden="true"><path fill="var(--teal)" d="M6.6 10.8a15.1 15.1 0 0 0 6.6 6.6l2.2-2.2a1 1 0 0 1 1-.25 11.4 11.4 0 0 0 3.6.57 1 1 0 0 1 1 1V20a1 1 0 0 1-1 1A17 17 0 0 1 3 4a1 1 0 0 1 1-1h3.5a1 1 0 0 1 1 1c0 1.25.2 2.45.57 3.57a1 1 0 0 1-.25 1z"/></svg>
      </li>
      <li>hlelectricalsolutions@mailvento.com
        <svg viewBox="0 0 24 24" aria-hidden="true"><rect x="3" y="5" width="18" height="14" rx="2" fill="none" stroke="var(--teal)" stroke-width="2"/><path d="M3 7l9 6 9-6" fill="none" stroke="var(--teal)" stroke-width="2"/></svg>
      </li>
    </ul>
    <svg class="footer-band" viewBox="0 0 720 70" aria-hidden="true">
      <polygon points="0,44 462,44 484,10 720,10 720,70 0,70" fill="var(--teal)"/>
      <polygon points="0,34 456,34 476,4 486,4 466,40 0,40" fill="var(--stripe-gray)"/>
    </svg>
  </section>
</main>
</body>
</html>
```